Two flyers with cover pages for business services company

We need to create two double sided A4 flyers for our company. We are a company that provides professional services for businesses in Dubai, UAE.
Please note that there are two different flyers. The design must be identical. Each has a cover page. The cover page will be duplicated for both flyers.
Please note that we have added images of the Dubai skyline, clip art as place-hold/temporary images. These can be changed to be more fitting to your design. We prefer to have free images where possible but are open to purchasing Framevault images if required.
We have recommended a colour palet below. You are welcome to change some colours to be more fitting to the design. However, we must have black, white and blue and per the logo.
Target Market(s)
Businesses, entrepreneurs, professionals
Industry/Entity Type
Business Service
Requirements
Must have
- The cover page should be less crowded and more visual. So mostly images with our logo and tagline.

```html
<!DOCTYPE html>
<html lang="en">
<head>
<meta charset="utf-8">
<title>Norvale Flyers</title>
<link href="https://fonts.googleapis.com/css2?family=Barlow+Semi+Condensed:wght@400;500;600;700;800&family=Montserrat:wght@400;500;700&display=swap" rel="stylesheet">
<style>
  :root {
    --blue: #1a56ad;
    --blue-deep: #0f4a9e;
    --navy: #142a5a;
    --night: #23246a;
    --orange: #f39322;
    --ink: #1b1b1b;
    --white: #ffffff;
    --stage: #e9eaec;
  }
  * { margin: 0; padding: 0; box-sizing: border-box; }
  html, body { width: 1200px; height: 1200px; overflow: hidden; background: var(--stage); }
  body { position: relative; font-family: "Montserrat", sans-serif; color: var(--ink); }

  .flyer { position: absolute; width: 546px; height: 772px; background: var(--white); overflow: hidden; box-shadow: 0 4px 14px rgba(0,0,0,.15); }
  .flyer--offer { left: 46px; top: 86px; }
  .flyer--cover { left: 626px; top: 262px; background: var(--night); }

  .brand { display: flex; align-items: center; gap: 7px; font-family: "Montserrat", sans-serif; font-weight: 500; color: var(--ink); }
  .brand__dot { border-radius: 50%; background: var(--blue); flex: none; }

  /* offer flyer */
  .hero { position: absolute; left: 0; top: 0; width: 546px; height: 330px;
    background: linear-gradient(180deg, #9ccbee 0%, #c7e2f6 45%, #eef6fc 80%, #fff 100%); }
  .hero__brand { position: absolute; left: 50%; top: 24px; transform: translateX(-50%); font-size: 20px; }
  .hero__brand .brand__dot { width: 24px; height: 24px; }

  .headline { position: absolute; left: 49px; top: 263px; font-family: "Barlow Semi Condensed", sans-serif; font-weight: 700;
    font-size: 36px; line-height: 33px; color: var(--blue); letter-spacing: -0.5px; }
  .subline { position: absolute; left: 53px; top: 342px; font-family: "Barlow Semi Condensed", sans-serif; font-weight: 400; font-size: 16.5px; letter-spacing: -0.2px; }
  .tag { position: absolute; left: 49px; height: 23px; padding: 0 5px; background: var(--orange); color: var(--white); font-size: 13.5px; line-height: 23px; }
  .tag--one { top: 369px; }
  .tag--two { top: 396px; }

  .offer__title { position: absolute; left: 49px; top: 437px; font-family: "Barlow Semi Condensed", sans-serif; font-weight: 700; font-size: 20px; line-height: 20px; letter-spacing: -0.4px; }
  .offer__list { position: absolute; left: 32px; top: 482px; list-style: none; font-size: 11.5px; line-height: 14.3px; }
  .offer__list li { position: relative; padding-left: 17px; }
  .offer__list li::before { content: ""; position: absolute; left: 0; top: 3px; border-left: 9px solid var(--blue); border-top: 4px solid transparent; border-bottom: 4px solid transparent; }
  .offer__list b { font-weight: 700; }

  .guarantee-band { position: absolute; left: 477px; top: 454px; width: 69px; height: 108px; background: var(--navy); clip-path: polygon(0 0,100% 0,100% 100%,0 100%,0 92%,20% 92%,20% 0); }
  .guarantee { position: absolute; left: 346px; top: 442px; width: 154px; height: 110px; background: var(--blue-deep); padding: 5px; }
  .guarantee__frame { width: 100%; height: 100%; border: 1.5px solid var(--white); color: var(--white); text-align: center; font-family: "Barlow Semi Condensed", sans-serif; font-weight: 700; padding-top: 12px; }
  .guarantee__big { font-size: 28px; line-height: 26px; }
  .guarantee__mid { font-size: 18px; line-height: 17px; }
  .guarantee__small { font-size: 11px; line-height: 16px; }

  .director__photo { position: absolute; left: 46px; top: 584px; width: 85px; height: 90px; background: linear-gradient(180deg, #8a7a66, #3a3f4c); }
  .director { position: absolute; left: 138px; top: 603px; }
  .director__name { font-size: 15px; font-weight: 500; color: var(--blue); }
  .director__role { font-size: 8px; font-style: italic; font-weight: 500; margin-top: 2px; }
  .director .brand { font-size: 9px; margin-top: 7px; gap: 4px; }
  .director .brand__dot { width: 9px; height: 9px; }

  .contact { position: absolute; left: 264px; top: 602px; width: 220px; text-align: center; }
  .contact__call { font-family: "Barlow Semi Condensed", sans-serif; font-weight: 800; font-size: 11.5px; }
  .contact__phone { font-family: "Montserrat", sans-serif; font-weight: 700; font-size: 22px; line-height: 24px; color: var(--blue); }
  .contact__info { font-size: 6.4px; line-height: 9px; }

  .footer { position: absolute; left: 0; bottom: 0; width: 546px; height: 88px; background: var(--orange); display: flex; align-items: center; }
  .flyer--offer .footer { border-top: 2px solid var(--ink); height: 90px; }
  .footer .brand { font-size: 27px; width: 250px; justify-content: center; }
  .footer .brand__dot { width: 30px; height: 30px; }
  .footer__divider { width: 1px; height: 46px; background: rgba(0,0,0,.15); }
  .footer__url { flex: 1; text-align: center; font-size: 24px; letter-spacing: 5px; color: #333; font-weight: 400; }

  /* cover flyer */
  .cover__scene { position: absolute; left: 0; top: 160px; width: 546px; height: 525px;
    background: linear-gradient(180deg, var(--night) 0%, #3f57a8 40%, #8d7fbf 62%, #c26a9d 74%, #2b2a4a 86%, #171826 100%); }
  .cover__title { position: absolute; left: 0; top: 76px; width: 546px; text-align: center; font-family: "Barlow Semi Condensed", sans-serif;
    font-weight: 700; font-size: 42px; line-height: 37px; color: var(--orange); letter-spacing: -0.5px; }
</style>
</head>
<body>

<article class="flyer flyer--offer">
  <div class="hero" role="img" aria-label="Photo of two businessmen shaking hands in front of a glass office building"></div>
  <div class="brand hero__brand"><span class="brand__dot"></span>Norvale</div>

  <h1 class="headline">DO YOU NEED HELP TO<br>INCREASE YOUR SALES ?</h1>
  <p class="subline">GROW YOUR BUSINESS THROUGH OUR EXTENSIVE NETWORK</p>
  <p class="tag tag--one">3000+ Business Connections</p>
  <p class="tag tag--two">570+ Decision Makers, MDs, CEO’s, Head of Purchasing</p>

  <h2 class="offer__title">THE BEST OFFER<br>IN THE SPONSORSHIP</h2>
  <ul class="offer__list">
    <li><b>50% off</b> your current sponsorship fees</li>
    <li>Free sponsorship for 12 months</li>
    <li>Low monthly installments (starting at&nbsp; AED 1,500)</li>
    <li>We are your active sponsor or strategic<br>partner if you are need us to be</li>
  </ul>

  <div class="guarantee-band"></div>
  <div class="guarantee">
    <div class="guarantee__frame">
      <div class="guarantee__big">100%</div>
      <div class="guarantee__mid">SATISFACTION<br>GUARANTEED</div>
      <div class="guarantee__small">OR YOUR MONEY BACK</div>
    </div>
  </div>

  <div class="director__photo" role="img" aria-label="Portrait photo of the managing director"></div>
  <div class="director">
    <p class="director__name">DANIEL HART</p>
    <p class="director__role">Managing Director</p>
    <div class="brand"><span class="brand__dot"></span>Norvale</div>
  </div>

  <div class="contact">
    <p class="contact__call">CALL US NOW FOR A FREE CONSULTANCY ON</p>
    <p class="contact__phone">04 555 0182</p>
    <p class="contact__info">Located at the Meridian Business Tower, 24th Floor Dubai, UAE<br>Sunday – Thursday: 9:00 am -18:00 pm</p>
  </div>

  <footer class="footer">
    <div class="brand"><span class="brand__dot"></span>Norvale</div>
    <span class="footer__divider"></span>
    <p class="footer__url">www.norvale.ae</p>
  </footer>
</article>

<article class="flyer flyer--cover">
  <div class="cover__scene" role="img" aria-label="Photo of the Dubai skyline at dusk with illuminated towers"></div>
  <h1 class="cover__title">YOUR BUSINESS<br>OUR CONNECTIONS</h1>
  <footer class="footer">
    <div class="brand"><span class="brand__dot"></span>Norvale</div>
    <span class="footer__divider"></span>
    <p class="footer__url">www.norvale.ae</p>
  </footer>
</article>

</body>
</html>
```